Birchline Septic Solutions

Would like to see some single sided ones but would also like to see some double sided with one sided only being the logo. Owners name is Colin Vandro. Phone number is 555-214-0387
Services are pumping, inspections, installs, and repairs

Contact Information for Business Card

555-241-0387 Colin Vandro Larkfield, OH

```html
<!DOCTYPE html>
<html lang="en">
<head>
<meta charset="utf-8">
<title>Birchline Septic Solutions – Business Card</title>
<link href="https://fonts.googleapis.com/css2?family=Montserrat:wght@400;500;700;800&display=swap" rel="stylesheet">
<style>
  :root {
    --teal: #05b8b2;
    --ink: #111111;
    --paper: #ffffff;
    --stage: #2b2b2b;
    --grey: #3a3a3a;
  }
  * { margin: 0; padding: 0; box-sizing: border-box; }
  html, body { width: 1200px; height: 880px; overflow: hidden; }
  body {
    background: var(--stage);
    font-family: 'Montserrat', sans-serif;
    position: relative;
  }
  .card {
    position: absolute;
    width: 560px;
    height: 320px;
    overflow: hidden;
    box-shadow: 0 10px 24px rgba(0,0,0,.45);
  }
  /* front side */
  .card-front {
    left: 60px; top: 110px;
    background: var(--teal);
    color: var(--paper);
  }
  .front-brand {
    position: absolute;
    left: 0; right: 0; top: 70px;
    text-align: center;
  }
  .brand-name {
    font-weight: 800;
    font-size: 30px;
    letter-spacing: 1px;
    line-height: 1.15;
    text-transform: uppercase;
  }
  .brand-name .line { display: block; }
  .brand-mark {
    display: inline-block;
    width: 16px; height: 16px;
    border-radius: 50%;
    background: currentColor;
    margin-bottom: 10px;
  }
  .services {
    position: absolute;
    left: 0; right: 0; top: 206px;
    text-align: center;
    font-size: 17px;
    font-weight: 500;
    line-height: 1.5;
  }
  .tick {
    width: 14px; height: 14px;
    vertical-align: -1px;
    margin: 0 4px 0 6px;
  }
  /* back side */
  .card-back {
    left: 580px; top: 450px;
    background: var(--paper);
    color: var(--ink);
  }
  .back-swoosh { position: absolute; inset: 0; }
  .back-brand {
    position: absolute;
    left: 40px; top: 92px;
    width: 250px;
    text-align: center;
    color: var(--ink);
  }
  .back-brand .brand-name { font-size: 26px; }
  .divider {
    position: absolute;
    left: 310px; top: 62px;
    width: 2px; height: 132px;
    background: var(--teal);
  }
  .contact {
    position: absolute;
    left: 330px; top: 62px;
    width: 215px;
  }
  .owner-name {
    font-weight: 800;
    font-size: 18px;
    text-transform: uppercase;
    letter-spacing: .3px;
  }
  .owner-name .surname { color: var(--teal); }
  .owner-role {
    font-size: 12px;
    color: var(--grey);
    margin: 2px 0 10px;
  }
  .contact-lines {
    font-size: 12.5px;
    line-height: 1.4;
    display: flex;
    gap: 6px;
  }
  .phone-icon { width: 13px; height: 13px; margin-top: 2px; flex: none; }
</style>
</head>
<body>

<section class="card card-front" aria-label="Business card front">
  <div class="front-brand">
    <span class="brand-mark" aria-hidden="true"></span>
    <h1 class="brand-name"><span class="line">Birchline</span><span class="line">Septic Solutions</span></h1>
  </div>
  <p class="services">
    <svg class="tick" viewBox="0 0 14 14" aria-hidden="true"><circle cx="7" cy="7" r="6" fill="none" stroke="#fff" stroke-width="1.6"/><path d="M4 7.2l2 2 4-4.4" fill="none" stroke="#fff" stroke-width="1.6"/></svg>Services are pumping<br>
    <svg class="tick" viewBox="0 0 14 14" aria-hidden="true"><circle cx="7" cy="7" r="6" fill="none" stroke="#fff" stroke-width="1.6"/><path d="M4 7.2l2 2 4-4.4" fill="none" stroke="#fff" stroke-width="1.6"/></svg>inspections
    <svg class="tick" viewBox="0 0 14 14" aria-hidden="true"><circle cx="7" cy="7" r="6" fill="none" stroke="#fff" stroke-width="1.6"/><path d="M4 7.2l2 2 4-4.4" fill="none" stroke="#fff" stroke-width="1.6"/></svg>installs
    <svg class="tick" viewBox="0 0 14 14" aria-hidden="true"><circle cx="7" cy="7" r="6" fill="none" stroke="#fff" stroke-width="1.6"/><path d="M4 7.2l2 2 4-4.4" fill="none" stroke="#fff" stroke-width="1.6"/></svg>and repairs
  </p>
</section>

<section class="card card-back" aria-label="Business card back">
  <svg class="back-swoosh" viewBox="0 0 560 320" aria-hidden="true">
    <path d="M0,320 L0,292 Q320,268 560,120 L560,320 Z" fill="var(--teal)"/>
    <path d="M70,280 Q360,258 540,130 Q372,250 70,280 Z" fill="var(--ink)" stroke="var(--ink)" stroke-width="1.2"/>
  </svg>
  <div class="back-brand">
    <span class="brand-mark" aria-hidden="true"></span>
    <h2 class="brand-name"><span class="line">Birchline</span><span class="line">Septic Solutions</span></h2>
  </div>
  <div class="divider" aria-hidden="true"></div>
  <div class="contact">
    <p class="owner-name">Colin <span class="surname">Vandro</span></p>
    <p class="owner-role">Owners</p>
    <div class="contact-lines">
      <svg class="phone-icon" viewBox="0 0 24 24" aria-hidden="true"><path fill="var(--teal)" d="M6.6 10.8a15.1 15.1 0 0 0 6.6 6.6l2.2-2.2c.3-.3.7-.4 1-.2 1.1.4 2.3.6 3.6.6.6 0 1 .4 1 1V20c0 .6-.4 1-1 1A17 17 0 0 1 3 4c0-.6.4-1 1-1h3.5c.6 0 1 .4 1 1 0 1.3.2 2.5.6 3.6.1.3 0 .7-.2 1z"/></svg>
      <p>555-214-0387<br>555-241-0387 Colin Vandro<br>Larkfield, OH</p>
    </div>
  </div>
</section>

</body>
</html>
```